Business Cards Design for the electrical wholesaler: clean bold dynamic :)

We need a business card design that would follow our latest brand guidelines. As an electrical wholesaler we want to bring a fresh look and feel into the industry. The design should be clean bold and dynamic. It should come alive with the renewed energy of our green colour. Our grey colour should keep things balanced and complement the notion of maturity and responsibility. We employ Lato as a corporate font however are not bound by this font and we’re open to interpretation here.

Target Market(s)

Electrical contractors

Industry/Entity Type

Business

Contact Information for Business Card

Logo
Name & Surname: Halyna Dorosh
Job Title: Director of Marketing
Email: halya.dorosh@quillmail.example
Cell phone: XXX.XXX.XXXX
Address: 20517 - 87 Ave. Edmonton, AB, Canada. T6K 4N8
Business Phone: 780.555.0184
Website: www.brovix.example

Font styles to use
Other font styles liked:
• Lato

Requirements
Must have
• Logo & website
Nice to have
• Brand elements - some of them you may find in the attached Brand Guidelines (e.g. three lines on the background signifying "W")

```html
<!DOCTYPE html>
<html lang="en">
<head>
<meta charset="utf-8">
<title>Brovix business cards</title>
<link rel="stylesheet" href="https://fonts.googleapis.com/css2?family=Work+Sans:wght@400;500;600&display=swap">
<style>
  :root {
    --backdrop: #3a3330;
    --card: #1d1d1e;
    --card-edge: #2a2a2b;
    --green: #8cc63f;
    --white: #f2f2f2;
    --grey: #d6d6d6;
  }
  * { margin: 0; padding: 0; box-sizing: border-box; }
  html, body {
    width: 1200px;
    height: 715px;
    overflow: hidden;
    background: var(--backdrop);
    font-family: "Work Sans", Arial, sans-serif;
  }
  .stage { position: relative; width: 1200px; height: 715px; }
  .card {
    position: absolute;
    width: 520px;
    height: 297px;
    background: var(--card);
    border: 1px solid var(--card-edge);
    border-radius: 3px;
    box-shadow: 0 14px 30px rgba(0,0,0,.45);
  }
  .card--front { left: 50px; top: 100px; display: flex; align-items: center; justify-content: center; }
  .card--back { left: 630px; top: 318px; display: flex; align-items: center; padding: 0 34px; }

  .wordmark { display: flex; align-items: center; gap: 12px; color: var(--white); font-weight: 600; }
  .wordmark__square { background: var(--green); }
  .card--front .wordmark { font-size: 76px; letter-spacing: -1px; }
  .card--front .wordmark__square { width: 40px; height: 40px; }
  .card--back .wordmark { font-size: 40px; letter-spacing: -0.5px; gap: 8px; }
  .card--back .wordmark__square { width: 22px; height: 22px; }

  .divider { width: 2px; height: 136px; background: var(--green); margin: 0 22px 0 26px; }

  .contact { color: var(--white); font-size: 13px; line-height: 1.45; }
  .contact__name { color: var(--green); font-size: 20px; font-weight: 500; line-height: 1.1; }
  .contact__role { color: var(--grey); font-size: 13px; margin-bottom: 6px; }
  .contact__line { display: flex; align-items: center; gap: 7px; }
  .contact__line svg { width: 9px; height: 9px; flex: none; }
  .contact__line--plain { padding-left: 16px; }
</style>
</head>
<body>
<div class="stage">
  <section class="card card--front">
    <div class="wordmark"><span class="wordmark__square"></span>brovix</div>
  </section>

  <section class="card card--back">
    <div class="wordmark"><span class="wordmark__square"></span>brovix</div>
    <div class="divider"></div>
    <div class="contact">
      <p class="contact__name">Halyna Dorosh</p>
      <p class="contact__role">Founder</p>
      <p class="contact__line contact__line--plain">20517 87ave</p>
      <p class="contact__line contact__line--plain">T6K4N8 Edmonton, Alberta</p>
      <p class="contact__line">
        <svg viewBox="0 0 10 10"><path d="M2 1h2l1 2.5-1.3.8a5 5 0 0 0 2 2l.8-1.3L9 6v2a1 1 0 0 1-1 1A7 7 0 0 1 1 2a1 1 0 0 1 1-1z" fill="var(--green)"/></svg>
        780.555.0184</p>
      <p class="contact__line">
        <svg viewBox="0 0 10 10"><rect x="0.5" y="2" width="9" height="6" fill="none" stroke="var(--green)"/><path d="M.5 2 5 5.5 9.5 2" fill="none" stroke="var(--green)"/></svg>
        halya.dorosh@quillmail.example</p>
      <p class="contact__line">
        <svg viewBox="0 0 10 10"><circle cx="5" cy="5" r="4.5" fill="var(--green)"/></svg>
        www.brovix.example</p>
    </div>
  </section>
</div>
</body>
</html>
```